Torvane Halbridge

Looking for modern business cards.
Clean contemporary design.
Similar to this.
https://www.plumvexa-search.example/imgres?imgurl=https%3A%2F%2Fimg.quorlint-cdn.example%2Fsleek_dark_metal_card_design_540.jpg&imgrefurl=https%3A%2F%2Fwww.quorlint-prints.example%2Fsleek_dark_metal_card_design-918273645501928374&q=modern%20business%20cards

But I'd like the blue to look metallic.

Business

```html
<!DOCTYPE html>
<html lang="en">
<head>
<meta charset="utf-8">
<title>Torvane Halbridge — Business Card</title>
<link rel="stylesheet" href="https://fonts.googleapis.com/css2?family=Roboto:ital,wght@0,400;0,500;0,700;1,700&display=swap">
<style>
  :root {
    --backdrop: #ebe8e4;
    --paper: #f3f3f3;
    --navy: #22566e;
    --teal: #259dbb;
    --teal-light: #3bb2cf;
    --teal-deep: #1f8aa6;
    --ink: #2a5470;
    --white: #ffffff;
  }
  * { margin: 0; padding: 0; box-sizing: border-box; }
  html, body {
    width: 1200px; height: 960px; overflow: hidden;
    background: var(--backdrop);
    font-family: "Roboto", Arial, sans-serif;
  }
  .card {
    position: absolute; width: 600px; height: 343px;
    box-shadow: 0 3px 8px rgba(0,0,0,.35);
    overflow: hidden;
  }
  .card-front { left: 314px; top: 113px; background: var(--paper); }
  .card-back {
    left: 311px; top: 472px;
    background: linear-gradient(135deg, var(--teal-light) 0%, var(--teal) 45%, var(--teal-deep) 100%);
  }

  .brand {
    position: absolute; left: 0; right: 0; top: 0; height: 215px;
    display: flex; flex-direction: column; align-items: center; justify-content: center;
    padding-top: 30px;
  }
  .brand-line { display: flex; align-items: center; gap: 10px; }
  .brand-dot { width: 14px; height: 14px; border-radius: 50%; background: var(--teal); }
  .brand-name { font-size: 32px; font-weight: 400; color: var(--ink); letter-spacing: -0.5px; }
  .tagline {
    margin-top: 6px; font-size: 7px; font-weight: 700; font-style: italic;
    color: var(--teal); letter-spacing: 0.6px;
  }

  .contact-band { position: absolute; left: 0; right: 0; top: 215px; height: 128px; display: flex; }
  .person {
    width: 300px; background: var(--navy); color: var(--white);
    padding: 20px 0 0 31px;
  }
  .person-name { font-size: 20px; font-weight: 500; letter-spacing: 0.2px; }
  .person-role { font-size: 14.5px; margin-top: 4px; }
  .person-address { font-size: 14.5px; margin-top: 6px; line-height: 19px; font-style: normal; }
  .divider { width: 2px; background: var(--white); }
  .reach {
    flex: 1; background: linear-gradient(135deg, var(--teal-light), var(--teal) 60%);
    color: var(--white); list-style: none;
    padding: 32px 31px 0 0; font-size: 14.5px;
  }
  .reach li { display: flex; justify-content: flex-end; align-items: center; height: 19.5px; gap: 10px; }
  .reach svg { width: 14px; height: 14px; fill: var(--white); }

  .back-brand {
    position: absolute; left: 0; right: 0; top: 138px;
    display: flex; justify-content: center; align-items: center; gap: 14px;
  }
  .back-dot { width: 22px; height: 22px; border-radius: 50%; background: var(--white); }
  .back-name { font-size: 40px; font-weight: 400; color: var(--white); }
  .web {
    position: absolute; left: 0; right: 0; top: 299px; text-align: center;
    color: var(--white); font-size: 14px; letter-spacing: 3px;
  }
</style>
</head>
<body>
  <section class="card card-front">
    <header class="brand">
      <div class="brand-line">
        <span class="brand-name">Torvane Halbridge</span>
        <span class="brand-dot"></span>
      </div>
      <p class="tagline">“Practical leadership for growing companies”</p>
    </header>
    <div class="contact-band">
      <div class="person">
        <h1 class="person-name">CORVIN DALEWOOD</h1>
        <p class="person-role">CEO/FOUNDER</p>
        <address class="person-address">214 Halvey Street<br>Marrowby, Oregon 97402</address>
      </div>
      <div class="divider"></div>
      <ul class="reach">
        <li>555 210 4471
          <svg viewBox="0 0 16 16"><path d="M3.6 1l2.6 2.8-1.4 2a9 9 0 0 0 5.4 5.4l2-1.4L15 12.4 13.4 15C6.8 15 1 9.2 1 2.6z"/></svg>
        </li>
        <li>555 318 2290
          <svg viewBox="0 0 16 16"><path d="M4 0h8a1 1 0 0 1 1 1v14a1 1 0 0 1-1 1H4a1 1 0 0 1-1-1V1a1 1 0 0 1 1-1zm1 2v10h6V2zm3 11a1 1 0 1 0 0 2 1 1 0 0 0 0-2z"/></svg>
        </li>
        <li>555 406 7713
          <svg viewBox="0 0 16 16"><path d="M4 1h8v4H4zM1 6h14v6h-2v3H3v-3H1zm4 5v2h6v-2z"/></svg>
        </li>
        <li>hello@torvane.example
          <svg viewBox="0 0 16 16"><path d="M1 3h14v1L8 9 1 4zm0 3l7 5 7-5v7H1z"/></svg>
        </li>
      </ul>
    </div>
  </section>

  <section class="card card-back">
    <div class="back-brand">
      <span class="back-name">Torvane Halbridge</span>
      <span class="back-dot"></span>
    </div>
    <p class="web">www.torvanehalbridge.example</p>
  </section>
</body>
</html>
```